Korval Advise Business Cards

We need a business card design for Korval Advise (Logo Attached), a management consultancy specialized in brand & business building.

Design should be clean, smart and a touch of innnovation without being gimmicky.

The details on the card should be:
Name: Tomas Velduren
Title: Managing Director
Address: 42 Marlowe Pier, Tarn Vessel Tower, Singapore 073926
Tel: +6285927461082
email: tv@korvaladvise.example
website: korvaladvise.example

For further background on corporate identity, please check www.korvaladvise.example
Updates

Dear all,

Many thanks for the submissions so far! I gave feedback to those designs that I prefer at this stage.

Overall I see that my preference goes into the direction that 'less is more' and 'simple is beautiful'

Please create uniqueness and standout by the simplicity and attraction of the overall concept and design.

Many thanks and please shout incase of questions!

Tomas

Industry/Entity Type

Business

```html
<!DOCTYPE html>
<html lang="en">
<head>
<meta charset="utf-8">
<title>Korval Advise Business Cards</title>
<link href="https://fonts.googleapis.com/css2?family=Open+Sans:wght@400;600;700&display=swap" rel="stylesheet">
<style>
  :root {
    --orange: #ff6a00;
    --charcoal: #4a4a4a;
    --charcoal-soft: #5a5a5a;
    --ink: #3a3a3a;
    --white: #ffffff;
    --backdrop: #e6e4e1;
  }
  * { box-sizing: border-box; margin: 0; padding: 0; }
  html, body { width: 1173px; height: 1200px; overflow: hidden; }
  body {
    background: var(--backdrop);
    font-family: "Open Sans", Arial, sans-serif;
    position: relative;
  }
  .card {
    position: absolute;
    width: 944px;
    height: 538px;
    overflow: hidden;
    box-shadow: 0 2px 8px rgba(0,0,0,0.18);
  }
  .card-front { left: 34px; top: 55px; background: var(--white); }
  .card-back { left: 203px; top: 631px; background: var(--orange); }

  .wordmark {
    position: absolute;
    font-weight: 600;
    white-space: nowrap;
    line-height: 1;
  }
  .card-front .wordmark {
    left: 96px; top: 62px;
    font-size: 70px;
    color: var(--charcoal);
  }
  .card-back .wordmark {
    left: 0; right: 0; top: 186px;
    text-align: center;
    font-size: 82px;
    color: var(--white);
  }

  .contact-list {
    position: absolute;
    left: 96px; top: 226px;
    list-style: none;
    font-size: 22px;
    color: var(--ink);
  }
  .contact-list li {
    display: flex; align-items: center;
    height: 41px;
  }
  .contact-icon { width: 20px; height: 20px; margin-right: 10px; flex: none; }

  .address {
    position: absolute;
    left: 96px; top: 384px;
    font-size: 22px;
    line-height: 33px;
    color: var(--ink);
    font-style: normal;
  }

  .base-band {
    position: absolute;
    left: 0; right: 0; bottom: 0;
    height: 78px;
    background: linear-gradient(90deg, var(--orange) 0%, var(--charcoal) 45%, var(--charcoal-soft) 100%);
  }

  .person {
    position: absolute;
    right: 40px; top: 464px;
    text-align: right;
    color: var(--white);
  }
  .person-name { font-size: 28px; font-weight: 700; line-height: 36px; }
  .person-title { font-size: 22px; line-height: 32px; }

  .back-url {
    position: absolute;
    left: 0; right: 0; top: 376px;
    text-align: center;
    font-size: 22px;
    letter-spacing: 5px;
    color: var(--white);
  }
</style>
</head>
<body>

<section class="card card-front" aria-label="Business card front">
  <div class="base-band" role="img" aria-label="Decorative band in charcoal and orange"></div>

  <div class="wordmark">Korval Advise</div>

  <ul class="contact-list">
    <li>
      <svg class="contact-icon" viewBox="0 0 20 20" aria-hidden="true">
        <circle cx="10" cy="10" r="9" fill="var(--orange)"/>
        <path d="M6.5 5.5 L8.5 5.5 L9.3 8 L8 9 C8.6 10.4 9.6 11.4 11 12 L12 10.7 L14.5 11.5 L14.5 13.5 C10 13.8 6.2 10 6.5 5.5 Z" fill="var(--white)"/>
      </svg>
      +6285927461082
    </li>
    <li>
      <svg class="contact-icon" viewBox="0 0 20 20" aria-hidden="true">
        <rect x="1" y="5" width="18" height="12" rx="1.5" fill="var(--orange)"/>
        <path d="M2 6 L10 12 L18 6" fill="none" stroke="var(--white)" stroke-width="1.6"/>
      </svg>
      tv@korvaladvise.example
    </li>
    <li>
      <svg class="contact-icon" viewBox="0 0 20 20" aria-hidden="true">
        <circle cx="10" cy="10" r="8.5" fill="var(--orange)"/>
        <g fill="none" stroke="var(--white)" stroke-width="1.1">
          <ellipse cx="10" cy="10" rx="3.5" ry="8.5"/>
          <line x1="1.5" y1="10" x2="18.5" y2="10"/>
          <line x1="3" y1="6" x2="17" y2="6"/>
          <line x1="3" y1="14" x2="17" y2="14"/>
        </g>
      </svg>
      www.korvaladvise.example
    </li>
  </ul>

  <address class="address">
    42 Marlowe Pier, Tarn<br>
    Vessel Tower, Singapore 073926
  </address>

  <div class="person">
    <div class="person-name">Tomas Velduren</div>
    <div class="person-title">Managing Director</div>
  </div>
</section>

<section class="card card-back" aria-label="Business card back">
  <div class="wordmark">Korval Advise</div>
  <div class="back-url">www.korvaladvise.example</div>
</section>

</body>
</html>
```